Quorva - corporate Business Card

We need a good look and innovative business card for a new start up company based in Los Angeles called "Quorva". We are in a payment business, including payment card, app, and ewallet. We are expert in online payment and Card not present (CNP) transaction.
We need an innovative, modern business card.

Our logo font is Aero Matics

Target Market(s)

Startup - Bank - Online Payment - Card Manufacturing

Industry/Entity Type

Startup

Contact Information for Business Card

phone: 555 014 7396 - Address: 4172 Marlowe blvd, Cylver City, CA 90299

Requirements
Must have
• Message: innovative, professional, expert, high tech, trust, online payment expert, security
Nice to have
• no comment
Should not have
• no Comment

```html
<!DOCTYPE html>
<html lang="en">
<head>
<meta charset="utf-8">
<title>Quorva — Business Card</title>
<link rel="stylesheet" href="https://fonts.googleapis.com/css2?family=Open+Sans:wght@400;700&display=swap">
<style>
  :root {
    --backdrop: #222222;
    --brand-red: #b5202e;
    --paper: #ffffff;
    --blush: #f5e3de;
    --ink-grey: #8a8a8a;
  }
  * { margin: 0; padding: 0; box-sizing: border-box; }
  html, body {
    width: 1189px;
    height: 1200px;
    overflow: hidden;
    background: var(--backdrop);
    font-family: "Open Sans", Arial, sans-serif;
  }
  .card {
    position: absolute;
    left: 171px;
    width: 856px;
    height: 487px;
    border-radius: 23px;
    overflow: hidden;
  }
  .card--front { top: 68px; background: var(--brand-red); }
  .card--back  { top: 626px; background: var(--paper); }

  .brand-lockup {
    position: absolute;
    left: 189px;
    top: 171px;
    display: flex;
    align-items: center;
    gap: 16px;
  }
  .brand-lockup__dot {
    width: 146px;
    height: 146px;
    border-radius: 50%;
    background: var(--paper);
  }
  .brand-lockup__name {
    color: var(--paper);
    font-weight: 700;
    font-size: 90px;
    letter-spacing: 2px;
    line-height: 1;
    margin-top: -6px;
  }

  .back-circle {
    position: absolute;
    left: -72px;
    top: 16px;
    width: 454px;
    height: 454px;
    border-radius: 50%;
    background: var(--blush);
  }
  .contact {
    position: absolute;
    left: 563px;
    top: 152px;
    color: var(--ink-grey);
    font-size: 23px;
    line-height: 28px;
  }
  .contact__name {
    color: var(--brand-red);
    font-weight: 700;
    font-size: 29px;
    line-height: 30px;
  }
  .contact__role { margin-bottom: 20px; line-height: 24px; }
  .contact__address { margin-bottom: 17px; }
  .contact__label { color: var(--brand-red); font-weight: 700; }
</style>
</head>
<body>
  <section class="card card--front">
    <div class="brand-lockup">
      <div class="brand-lockup__dot"></div>
      <div class="brand-lockup__name">quorva</div>
    </div>
  </section>

  <section class="card card--back">
    <div class="back-circle"></div>
    <div class="contact">
      <div class="contact__name">Elena Brandt</div>
      <div class="contact__role">Managing Director</div>
      <div class="contact__address">4172 Marlowe blvd,<br>Halvern Falls, OR 90299</div>
      <div class="contact__phone"><span class="contact__label">P:</span> 555 014 7396</div>
    </div>
  </section>
</body>
</html>
```